High Tech Real Estate Startup needs a business card

We are developing an innovative real estate marketing product based around advanced search and virtual reality.

We talk to people, we need business cards.

Target Market(s)

The target market is technology professionals and realtors.

Contact Information for Business Card

The information to be included will include

Name
Title
Phone Number
E-mail Address
www.zelquin.com

It should use simple iconography for each one of those fields.

Font styles to use
Other font styles liked:
• Co, Jubilat, Avenir

Colors

Designer to choose colors to be used in the design.

Requirements
Must have
• Clean aesthetic,
• Good use of negative space.
• It should use our company logo, shown in the attached file. It is able to use the negative of that logo (coloured font and white background) and I have attached other acceptable accent colours in a swatch file.
Should not have
• Should not be too busy
• No extraneous text (slogans, tag lines etc)

```html
<!DOCTYPE html>
<html lang="en">
<head>
<meta charset="utf-8">
<title>Zelquin Business Card</title>
<link href="https://fonts.googleapis.com/css2?family=Open+Sans:wght@400;600;700&display=swap" rel="stylesheet">
<style>
  :root {
    --backdrop: #2c2c2d;
    --card-black: #1d1e20;
    --logo-gloss: #3a3b3e;
    --teal: #46b4b6;
    --curve-grey: #40474b;
    --white: #ffffff;
  }
  * { margin: 0; padding: 0; box-sizing: border-box; }
  html, body {
    width: 799px;
    height: 1200px;
    overflow: hidden;
    background: var(--backdrop);
    font-family: "Open Sans", sans-serif;
  }
  .card {
    position: absolute;
    left: 100px;
    width: 600px;
    height: 343px;
    border-radius: 22px;
    overflow: hidden;
    background: var(--card-black);
  }
  .card--front { top: 140px; }
  .card--back { top: 720px; }

  .front-logo {
    position: absolute;
    inset: 0;
    display: flex;
    align-items: center;
    justify-content: center;
    font-size: 68px;
    font-weight: 600;
    letter-spacing: 4px;
    color: var(--logo-gloss);
  }

  .back-art { position: absolute; inset: 0; }

  .back-logo {
    position: absolute;
    left: 36px;
    top: 144px;
    font-size: 42px;
    font-weight: 600;
    letter-spacing: 2px;
    line-height: 1;
    color: var(--teal);
  }

  .contact {
    position: absolute;
    left: 340px;
    top: 118px;
    color: var(--white);
  }
  .contact__name { font-size: 24px; font-weight: 700; line-height: 1.15; }
  .contact__title { font-size: 14px; font-weight: 600; margin-bottom: 14px; }
  .contact__list { list-style: none; }
  .contact__item {
    display: flex;
    align-items: center;
    gap: 10px;
    font-size: 16px;
    font-weight: 600;
    line-height: 24px;
  }
  .contact__icon { width: 16px; height: 16px; flex: none; }
</style>
</head>
<body>

<section class="card card--front" aria-label="Card front">
  <div class="front-logo">ZELQUIN</div>
</section>

<section class="card card--back" aria-label="Card back">
  <svg class="back-art" viewBox="0 0 600 343" width="600" height="343" aria-hidden="true">
    <rect width="600" height="343" fill="var(--teal)"/>
    <path d="M0 0 H335 C300 150 250 270 170 343 H0 Z" fill="var(--curve-grey)"/>
    <path d="M0 0 H322 C288 148 232 265 150 343 H0 Z" fill="var(--card-black)"/>
  </svg>

  <div class="back-logo">ZELQUIN</div>

  <div class="contact">
    <div class="contact__name">Mara Lenn Ostby</div>
    <div class="contact__title">Managing Director</div>
    <ul class="contact__list">
      <li class="contact__item">
        <svg class="contact__icon" viewBox="0 0 16 16" aria-hidden="true">
          <circle cx="8" cy="8" r="7.5" fill="none" stroke="#fff" stroke-width="1"/>
          <path d="M5 4.5 L6.5 4 L7.3 6 L6.4 6.7 Q7.2 8.6 9.2 9.6 L9.9 8.7 L11.9 9.5 L11.4 11 Q7.5 11.5 5 4.5 Z" fill="#fff"/>
        </svg>
        555.019.4821
      </li>
      <li class="contact__item">
        <svg class="contact__icon" viewBox="0 0 16 16" aria-hidden="true">
          <circle cx="8" cy="8" r="7.5" fill="none" stroke="#fff" stroke-width="1"/>
          <rect x="4" y="5" width="8" height="6" fill="none" stroke="#fff" stroke-width="1"/>
          <path d="M4 5 L8 8.5 L12 5" fill="none" stroke="#fff" stroke-width="1"/>
        </svg>
        mara@zelquin.com
      </li>
      <li class="contact__item">
        <svg class="contact__icon" viewBox="0 0 16 16" aria-hidden="true">
          <circle cx="8" cy="8" r="7.5" fill="none" stroke="#fff" stroke-width="1"/>
          <circle cx="8" cy="8" r="4" fill="none" stroke="#fff" stroke-width="1"/>
          <path d="M4 8 H12 M8 4 Q5.5 8 8 12 Q10.5 8 8 4" fill="none" stroke="#fff" stroke-width="0.8"/>
        </svg>
        www.zelquin.com
      </li>
    </ul>
  </div>
</section>

</body>
</html>
```